Visit card

Industry/Entity Type

Health Care

Contact Information for Business Card

O VITALIS SYSTEMS
Odile Brevard - chef de Projet

Requirements
Must have
• 318 Gaston Lemaire Street 59710 CORVAINE Tel: 33 (0) 327 481 605 Mobile: 06 42 19 37 64 Web: www.quorvexsystems.example Contact: o.brevard@o-vitalissystems.example
Should not have
• Respect for color

```html
<!DOCTYPE html>
<html lang="fr">
<head>
<meta charset="utf-8">
<title>O Vitalis Systems – Carte de visite</title>
<link rel="stylesheet" href="https://fonts.googleapis.com/css2?family=Lato:wght@400;700&family=Montserrat:wght@700;800&display=swap">
<style>
  :root {
    --page: #d9d9db;
    --charcoal: #3d3d3f;
    --red: #e31e2b;
    --white: #ffffff;
    --ink: #2c2c2e;
    --faint: #f3f3f4;
  }
  * { box-sizing: border-box; margin: 0; padding: 0; }
  html, body { width: 1200px; height: 900px; overflow: hidden; }
  body {
    background: var(--page);
    font-family: "Lato", Arial, sans-serif;
    position: relative;
  }
  .card {
    position: absolute;
    left: 250px;
    width: 700px;
    height: 400px;
    border-radius: 22px;
    overflow: hidden;
    box-shadow: 0 10px 28px rgba(0,0,0,.18);
  }

  /* Back side */
  .card-back { top: 36px; background: var(--charcoal); }
  .card-back .brand {
    position: absolute; left: 0; right: 0; top: 140px;
    display: flex; align-items: center; justify-content: center; gap: 26px;
  }
  .brand-dot {
    width: 96px; height: 96px; border-radius: 50%;
    background: var(--white); flex: none;
  }
  .brand-name {
    font-family: "Montserrat", Arial, sans-serif;
    font-weight: 800;
    font-size: 44px;
    letter-spacing: 1px;
    line-height: 1;
    color: var(--red);
    white-space: nowrap;
  }
  .back-rule {
    position: absolute; left: 0; right: 0; top: 318px;
    display: flex; align-items: center; gap: 18px;
  }
  .back-rule .line { flex: 1; height: 2px; background: var(--red); }
  .back-web { color: var(--white); font-size: 17px; letter-spacing: 2px; }
  .back-web .accent { color: var(--red); }

  /* Front side */
  .card-front { top: 466px; background: var(--white); }
  .front-watermark {
    position: absolute; right: 60px; top: 125px;
    width: 180px; height: 180px; border-radius: 50%;
    background: var(--faint);
  }
  .card-front .brand {
    position: absolute; right: 44px; top: 40px;
    display: flex; align-items: center; gap: 16px;
  }
  .card-front .brand-dot { width: 66px; height: 66px; background: var(--charcoal); }
  .card-front .brand-name { font-size: 29px; }

  .person { position: absolute; left: 58px; top: 128px; }
  .person-name {
    font-family: "Montserrat", Arial, sans-serif;
    font-weight: 800; font-size: 28px; color: var(--red);
    text-transform: uppercase; letter-spacing: .3px; line-height: 1.1;
  }
  .person-role { font-size: 18px; color: var(--ink); margin-top: 4px; }
  .person-rule { width: 100px; height: 2px; background: var(--red); margin-top: 8px; }

  .address {
    position: absolute; left: 58px; top: 204px;
    font-size: 16px; line-height: 1.3; color: var(--ink); font-style: normal;
  }
  .contacts {
    position: absolute; left: 74px; top: 274px;
    list-style: none; font-size: 15px; color: var(--ink);
  }
  .contacts li { display: flex; align-items: center; gap: 10px; line-height: 1.45; }
  .contacts svg { width: 14px; height: 14px; flex: none; fill: var(--red); }

  .front-bands { position: absolute; left: 0; bottom: 0; width: 100%; height: 42px; }
</style>
</head>
<body>

<section class="card card-back" aria-label="Verso de la carte">
  <div class="brand">
    <span class="brand-dot"></span>
    <span class="brand-name">O VITALIS SYSTEMS</span>
  </div>
  <div class="back-rule">
    <span class="line"></span>
    <span class="back-web">www.<span class="accent">quorvexsystems</span>.example</span>
    <span class="line"></span>
  </div>
</section>

<section class="card card-front" aria-label="Recto de la carte">
  <span class="front-watermark"></span>
  <div class="brand">
    <span class="brand-dot"></span>
    <span class="brand-name">O VITALIS SYSTEMS</span>
  </div>

  <div class="person">
    <h1 class="person-name">Odile Brevard</h1>
    <p class="person-role">Chef de Projet</p>
    <div class="person-rule"></div>
  </div>

  <address class="address">
    318<br>
    Rue Gaston Lemaire<br>
    59710 CORVAINE
  </address>

  <ul class="contacts">
    <li>
      <svg viewBox="0 0 16 16"><path d="M4 0h8a1 1 0 0 1 1 1v14a1 1 0 0 1-1 1H4a1 1 0 0 1-1-1V1a1 1 0 0 1 1-1zm1 2v10h6V2zm3 11a1 1 0 1 0 0 2 1 1 0 0 0 0-2z"/></svg>
      06 42 19 37 64
    </li>
    <li>
      <svg viewBox="0 0 16 16"><path d="M3.6 1 6 3.8 4.7 5.6a9 9 0 0 0 5.7 5.7l1.8-1.3L15 12.4 13.3 15C6.5 14.6 1.4 9.5 1 2.7z"/></svg>
      +33 (0) 327 481 605
    </li>
    <li>
      <svg viewBox="0 0 16 16"><path d="M0 3h16v1.4L8 9 0 4.4zm0 3.2 8 4.6 8-4.6V13H0z"/></svg>
      o.brevard@o-vitalissystems.example
    </li>
    <li>
      <svg viewBox="0 0 16 16"><path d="M8 0a8 8 0 1 0 0 16A8 8 0 0 0 8 0zm-1 1.6V5H4.4A6.4 6.4 0 0 1 7 1.6zm2 0A6.4 6.4 0 0 1 11.6 5H9zM1.8 7H7v2H1.8a6 6 0 0 1 0-2zm7.2 0h5.2a6 6 0 0 1 0 2H9zm-4.6 4H7v3.4A6.4 6.4 0 0 1 4.4 11zm4.6 0h2.6A6.4 6.4 0 0 1 9 14.4z"/></svg>
      www.quorvexsystems.example
    </li>
  </ul>

  <svg class="front-bands" viewBox="0 0 700 42" preserveAspectRatio="none" aria-hidden="true">
    <polygon points="0,42 0,30 520,30 540,0 548,0 528,42" fill="var(--charcoal)"/>
    <polygon points="540,42 560,0 700,0 700,42" fill="var(--red)"/>
  </svg>
</section>

</body>
</html>
```